Kestova Information Posters for Student signage

Secondary school looking for some posters to display throughout the school with fresh designs using school colours and fitting with general feel of the school's graphic image. The final designs should be welcoming but clearly outline the required instructions. Sample designs that have been created by the school are attached with the relevant information that is required to appear on the signs. School would like a more dynamic design than the basic signs attached.
We are looking for:
- Large pop-up banner style size for the 2 posters called
"Ready for class" and "Morning Routine".
- Printable poster for the "Kestova Outdoor" sign.

Please incorporate a design feature of "the Kestova 1,2,3" into the posters and also use the Kestova Leaner values of Integrity, Compassion, Curiosity and Drive to help illustrate the content.

An option for design is to incorporate our school's first nations artwork into the design and i have also provided various extracts of design pieces that the school often uses in it's marketing materials.

Target Market(s)

Secondary School Students

Industry/Entity Type

Education

Colors
00AB8E
00BBA5
67D7C9
C6EFE9
E9F9F6
FFF300
FFF600
FEFA6F
FFFEC7
FFFEE8
FFC000
F8CF3A
FAE287
FDF2CF
FEFAEE

Requirements
Must have
• My project must have eyecatching graphics

```html
<!DOCTYPE html>
<html lang="en">
<head>
<meta charset="utf-8">
<title>Morning Routine – Kestova</title>
<link href="https://fonts.googleapis.com/css2?family=Poppins:wght@700;800&family=Tinos:ital,wght@1,700&display=swap" rel="stylesheet">
<style>
  :root {
    --green: #224e35;
    --green-soft: #8a9d8c;
    --yellow: #fde725;
    --white: #ffffff;
    --dots: #b9b9b9;
  }
  * { margin: 0; padding: 0; box-sizing: border-box; }
  html, body { width: 1200px; height: 2823px; overflow: hidden; background: var(--white); }
  .poster { position: relative; width: 1200px; height: 2823px; overflow: hidden; font-family: "Poppins", sans-serif; color: var(--green); }
  .backdrop { position: absolute; inset: 0; }
  .title {
    position: absolute; top: 232px; left: 0; width: 1200px; text-align: center;
    font-weight: 800; font-size: 186px; line-height: 146px; letter-spacing: -3px; text-transform: uppercase;
  }
  .steps-pill {
    position: absolute; left: 64px; top: 573px; width: 1070px; height: 172px;
    border: 9px solid var(--yellow); border-radius: 60px; background: var(--white); overflow: hidden;
  }
  .steps-pill .name {
    position: absolute; left: 0; top: 0; bottom: 0; width: 656px; background: var(--yellow);
    font-weight: 700; font-size: 90px; line-height: 154px; padding-left: 28px; letter-spacing: -1px;
  }
  .num {
    position: absolute; border-radius: 50%; background: var(--green); color: var(--white);
    font-weight: 800; text-align: center;
  }
  .steps-pill .num { width: 104px; height: 104px; top: 25px; font-size: 66px; line-height: 108px; }
  .tagline {
    position: absolute; top: 780px; left: 0; width: 1200px; text-align: center;
    font-family: "Tinos", serif; font-style: italic; font-weight: 700; font-size: 72px; line-height: 90px;
  }
  .panel {
    position: absolute; left: 70px; width: 1057px; border: 9px solid var(--yellow); border-radius: 44px; background: var(--white);
  }
  .panel.on-time { top: 949px; height: 673px; }
  .panel.late { top: 1721px; height: 679px; }
  .panel-label {
    position: absolute; background: var(--yellow); border-radius: 28px; text-align: center;
    font-weight: 800; font-size: 68px; letter-spacing: -3px; text-transform: uppercase; line-height: 108px; height: 104px;
  }
  .row { position: absolute; left: 0; width: 1200px; height: 140px; }
  .row .num { left: 141px; top: 3px; width: 134px; height: 134px; font-size: 92px; line-height: 140px; }
  .row .icon { position: absolute; left: 312px; top: 3px; width: 134px; height: 134px; border-radius: 50%; background: var(--yellow); }
  .row .icon svg { width: 134px; height: 134px; }
  .row .text {
    position: absolute; left: 504px; top: 0; height: 140px; width: 580px; display: flex; align-items: center;
    font-weight: 700; font-size: 46px; line-height: 50px; letter-spacing: -0.5px;
  }
  .divider { position: absolute; left: 142px; width: 916px; border-top: 4px dotted var(--dots); }
  .values { position: absolute; right: 301px; top: 2646px; text-align: right; }
  .values .value { color: var(--white); font-weight: 800; font-size: 50px; line-height: 60px; }
  .values .caption { color: var(--yellow); font-weight: 700; font-size: 35px; line-height: 44px; font-family: "Poppins", sans-serif; }
  .school-mark { position: absolute; left: 930px; top: 2500px; width: 220px; text-align: center; }
  .school-mark .dot { width: 170px; height: 170px; border-radius: 50%; background: var(--yellow); margin: 0 auto 18px; }
  .school-mark .name { color: var(--yellow); font-weight: 800; font-size: 44px; line-height: 50px; }
</style>
</head>
<body>
<main class="poster">
  <svg class="backdrop" width="1200" height="2823" viewBox="0 0 1200 2823" aria-hidden="false">
    <path role="img" aria-label="Yellow First Nations dot artwork band" fill="var(--yellow)"
      d="M0 0 H1200 V40 C1050 120 900 200 700 220 C520 240 380 200 220 205 C120 208 50 215 0 220 Z"/>
    <path role="img" aria-label="Green First Nations dot artwork band" fill="var(--green)"
      d="M0 2515 C200 2470 420 2470 620 2500 C820 2520 900 2420 1000 2370 C1080 2330 1150 2325 1200 2320 V2823 H0 Z"/>
    <path fill="none" stroke="var(--green-soft)" stroke-width="14"
      d="M0 2605 C220 2555 420 2560 620 2590 C800 2615 900 2520 1000 2470 C1080 2430 1150 2422 1200 2418"/>
  </svg>

  <h1 class="title">Morning<br>Routine</h1>

  <div class="steps-pill">
    <div class="name">The Kestova</div>
    <div class="num" style="left:683px">1</div>
    <div class="num" style="left:810px">2</div>
    <div class="num" style="left:938px">3</div>
  </div>

  <p class="tagline">Early is on time, on time is late!</p>

  <section class="panel on-time"></section>
  <div class="panel-label" style="left:408px;top:902px;width:383px">On Time</div>

  <div class="row" style="top:1017px">
    <div class="num">1</div>
    <div class="icon"><svg viewBox="0 0 134 134"><circle cx="67" cy="67" r="38" fill="none" stroke="var(--green)" stroke-width="6"/><path d="M67 42 V68 L84 82" fill="none" stroke="var(--green)" stroke-width="6" stroke-linecap="round"/></svg></div>
    <div class="text">Arrive before<br>8:30 AM</div>
  </div>
  <div class="divider" style="top:1195px"></div>
  <div class="row" style="top:1232px">
    <div class="num">2</div>
    <div class="icon"><svg viewBox="0 0 134 134"><g fill="var(--green)"><rect x="27" y="32" width="25" height="70" rx="2"/><rect x="55" y="32" width="25" height="70" rx="2"/><rect x="83" y="32" width="25" height="70" rx="2"/></g><g stroke="var(--yellow)" stroke-width="3"><path d="M32 40h15M32 46h15M32 52h15M60 40h15M60 46h15M60 52h15M88 40h15M88 46h15M88 52h15"/></g></svg></div>
    <div class="text">Place Bag in<br>Locker</div>
  </div>
  <div class="divider" style="top:1399px"></div>
  <div class="row" style="top:1447px">
    <div class="num">3</div>
    <div class="icon"><svg viewBox="0 0 134 134"><g fill="var(--green)"><circle cx="67" cy="36" r="9"/><rect x="54" y="47" width="26" height="26" rx="4"/><rect x="44" y="68" width="46" height="8"/><rect x="30" y="56" width="10" height="24"/><rect x="96" y="52" width="10" height="28"/><circle cx="40" cy="88" r="7"/><circle cx="58" cy="86" r="7"/><circle cx="76" cy="86" r="7"/><circle cx="94" cy="88" r="7"/><rect x="28" y="96" width="78" height="12" rx="5"/></g></svg></div>
    <div class="text">Arrive at Home Group / House Assembly before 8:40 AM</div>
  </div>

  <section class="panel late"></section>
  <div class="panel-label" style="left:299px;top:1679px;width:600px">Running Late</div>

  <div class="row" style="top:1793px">
    <div class="num">1</div>
    <div class="icon"><svg viewBox="0 0 134 134"><g fill="var(--green)"><rect x="66" y="26" width="3" height="18"/><path d="M69 26h14l-4 5 4 5h-14z"/><path d="M50 58 L67 42 L84 58 Z"/><rect x="52" y="58" width="30" height="46"/><rect x="28" y="68" width="24" height="36"/><rect x="82" y="68" width="24" height="36"/><rect x="24" y="104" width="86" height="5"/></g><g fill="var(--yellow)"><rect x="62" y="86" width="10" height="18"/><rect x="34" y="76" width="5" height="8"/><rect x="42" y="76" width="5" height="8"/><rect x="88" y="76" width="5" height="8"/><rect x="96" y="76" width="5" height="8"/><rect x="60" y="66" width="5" height="8"/><rect x="70" y="66" width="5" height="8"/></g></svg></div>
    <div class="text">Sign in at<br>Student Services</div>
  </div>
  <div class="divider" style="top:1971px"></div>
  <div class="row" style="top:2008px">
    <div class="num">2</div>
    <div class="icon"><svg viewBox="0 0 134 134"><g fill="var(--green)"><rect x="27" y="32" width="25" height="70" rx="2"/><rect x="55" y="32" width="25" height="70" rx="2"/><rect x="83" y="32" width="25" height="70" rx="2"/></g><g stroke="var(--yellow)" stroke-width="3"><path d="M32 40h15M32 46h15M32 52h15M60 40h15M60 46h15M60 52h15M88 40h15M88 46h15M88 52h15"/></g></svg></div>
    <div class="text" style="align-items:flex-end;padding-bottom:22px">Place bag in Locker</div>
  </div>
  <div class="divider" style="top:2176px"></div>
  <div class="row" style="top:2223px">
    <div class="num">3</div>
    <div class="icon"><svg viewBox="0 0 134 134"><g fill="var(--green)"><circle cx="67" cy="36" r="9"/><rect x="54" y="47" width="26" height="26" rx="4"/><rect x="44" y="68" width="46" height="8"/><rect x="30" y="56" width="10" height="24"/><rect x="96" y="52" width="10" height="28"/><circle cx="40" cy="88" r="7"/><circle cx="58" cy="86" r="7"/><circle cx="76" cy="86" r="7"/><circle cx="94" cy="88" r="7"/><rect x="28" y="96" width="78" height="12" rx="5"/></g></svg></div>
    <div class="text">Prompt arrival to<br>class expected</div>
  </div>

  <div class="values">
    <div class="value">Integrity</div>
    <div class="caption">Kestova Learner Values</div>
  </div>

  <div class="school-mark">
    <div class="dot"></div>
    <div class="name">Kestova</div>
  </div>
</main>
</body>
</html>
```